Hardcore nerd needs to stand out in a sea of dull Defence business cards

Wombarra Devices is a new Australian consulting engineering company that turns research and theory into practical systems. No evangelistic fluff, just mathematics and physics into electronic and optical circuits for consumer products, scientific research or Defence applications.

We already have a recognised logo (provided) which is often dark blue/black on a light background but we're open to other combinations. (Us engineers tend to have limited aesthetic imagination :)

Some of our recent products have included:
* Instrumentation for electrical testing,
* Radar jammers,
* GPS antenna design,
* Satellite tracking systems,
* High power lasers

We're open to both single and double-sided designs - happy to be convinced either way.

P.S. Another group is working on the web page, so - alas - our web site is currently of no use for images/ideas...

Target Market(s)

Engineering managers,
Scientists

Contact Information for Business Card

Dr Colin Harte
R&D Engineer

colin@wombarradevices.com.au
0427 563 710

PO Box XXX (to be confirmed)
Kelsby ACT 2917
Australia

Font styles to use
Serif
Sans Serif

Colors

Designer to choose colors to be used in the design.

Requirements
Must have
• My contact details!
• I've had many (great) "bold and plain" designs submitted already, so feel free to be artistically creative :)
• Happy to take advice re fonts/colours/printability etc.
Nice to have
• I'm not sure if "lists" are more at home on a CV than a business card, but representative services include:
• Applied electromagnetics
• RF and high speed electronics
• Signal and image processing
• Electro-optical and laser systems
• Concept-to-prototype design services
• If you're considering double sided cards, then often measuring/alignment grids/rulers feature on the back of similar cards.
• e.g. https://www.veltranoptics.example/newgrouppage9.cfm?objectgroup_id=4183
• https://www.veltranoptics.example/newgrouppage9.cfm?objectgroup_ID=4185
• ..or even a "Smith chart" (google will return lots)
• Generic images to represent a capability might work - googling images associated with keyword for each of these areas might help:
• - "passive radar", "phased array", "fdtd", "vircator"
• RF and high speed electronic design
• - "smith chart", "microstrip circuits", "dimensioned drawing", "electronic schematic"
• - "dft", "iir filter"
• - "optical cavity". "laser energy level diagram"
• Background/watermarked images outlines/wireframes/schematics would probably look OK.
Should not have
• If a list of projects/services is provided, it is important not to make the client feel that this is "all" the company can do. Engineering design is a creative discipline (like graphics :)
• Please, no stock "military" snaps like planes, missiles, etc!

```html
<!DOCTYPE html>
<html lang="en">
<head>
<meta charset="utf-8">
<title>Wombarra Devices – Business Card</title>
<link href="https://fonts.googleapis.com/css2?family=Montserrat:wght@400;500;700;800&display=swap" rel="stylesheet">
<style>
  :root {
    --navy: #1f2a5f;
    --navy-deep: #182250;
    --paper: #f3f3f4;
    --stage: #5c5c5e;
    --white: #ffffff;
  }
  * { margin: 0; padding: 0; box-sizing: border-box; }
  html, body {
    width: 1200px;
    height: 911px;
    overflow: hidden;
  }
  body {
    background: var(--stage);
    font-family: "Montserrat", sans-serif;
    display: flex;
    flex-direction: column;
    align-items: center;
    justify-content: center;
    gap: 40px;
  }
  .card {
    width: 720px;
    height: 411px;
    position: relative;
    overflow: hidden;
    box-shadow: 0 10px 28px rgba(0, 0, 0, 0.35);
  }
  .card--front {
    background: var(--navy);
  }
  .card--back {
    background: var(--paper);
    border-bottom: 6px solid var(--navy);
  }
  .brand {
    position: absolute;
    display: flex;
    align-items: center;
    gap: 16px;
  }
  .brand__dot {
    width: 56px;
    height: 56px;
    border-radius: 50%;
    flex: none;
  }
  .brand__name {
    font-weight: 800;
    font-size: 30px;
    letter-spacing: 0.5px;
    text-transform: uppercase;
    line-height: 1;
    white-space: nowrap;
  }
  .card--front .brand {
    left: 84px;
    top: 178px;
  }
  .card--front .brand__dot { background: var(--white); }
  .card--front .brand__name { color: var(--white); }

  .card--back .brand {
    left: 54px;
    top: 238px;
    gap: 12px;
  }
  .card--back .brand__dot {
    background: var(--navy);
    width: 44px;
    height: 44px;
  }
  .card--back .brand__name {
    color: var(--navy);
    font-size: 20px;
    letter-spacing: 0.2px;
  }

  .divider {
    position: absolute;
    left: 376px;
    top: 150px;
    width: 2px;
    height: 170px;
    background: var(--navy);
  }
  .contact {
    position: absolute;
    left: 398px;
    top: 140px;
    right: 16px;
    color: var(--navy);
  }
  .contact__name {
    font-weight: 800;
    font-size: 22px;
    text-transform: uppercase;
    letter-spacing: 0.3px;
    white-space: nowrap;
  }
  .contact__role {
    font-weight: 500;
    font-size: 14px;
    margin-top: 2px;
    padding-left: 12px;
  }
  .contact__address {
    font-style: normal;
    font-weight: 500;
    font-size: 14px;
    line-height: 1.35;
    margin-top: 20px;
    padding-left: 20px;
  }
  .contact__lines {
    list-style: none;
    margin-top: 16px;
    padding-left: 30px;
    font-weight: 500;
    font-size: 14px;
    line-height: 1.5;
  }
  .contact__lines li {
    display: flex;
    align-items: center;
    gap: 7px;
    white-space: nowrap;
  }
  .contact__icon {
    width: 13px;
    height: 13px;
    fill: var(--navy);
    flex: none;
  }
</style>
</head>
<body>
  <section class="card card--front" aria-label="Card front">
    <div class="brand">
      <span class="brand__dot"></span>
      <span class="brand__name">Wombarra Devices</span>
    </div>
  </section>

  <section class="card card--back" aria-label="Card back">
    <div class="brand">
      <span class="brand__dot"></span>
      <span class="brand__name">Wombarra Devices</span>
    </div>
    <span class="divider"></span>
    <div class="contact">
      <p class="contact__name">Dr Colin Harte</p>
      <p class="contact__role">R&amp;D Engineer</p>
      <address class="contact__address">
        PO Box XXX<br>
        Kelsby ACT 2917, Australia
      </address>
      <ul class="contact__lines">
        <li>
          <svg class="contact__icon" viewBox="0 0 24 24" aria-hidden="true"><path d="M6.6 10.8a15.1 15.1 0 0 0 6.6 6.6l2.2-2.2c.3-.3.7-.4 1-.2 1.1.4 2.3.6 3.6.6.6 0 1 .4 1 1V20c0 .6-.4 1-1 1A17 17 0 0 1 3 4c0-.6.4-1 1-1h3.5c.6 0 1 .4 1 1 0 1.3.2 2.5.6 3.6.1.3 0 .7-.2 1z"/></svg>
          0427 563 710
        </li>
        <li>
          <svg class="contact__icon" viewBox="0 0 24 24" aria-hidden="true"><path d="M2 5h20v14H2z M3.5 6.5 12 13l8.5-6.5" stroke="#f3f3f4" stroke-width="1.6"/></svg>
          colin@wombarradevices.com.au
        </li>
      </ul>
    </div>
  </section>
</body>
</html>
```